Maple Beacon Website

We are starting a marketing company and to do that we need a website! We want a website that will inspire and persuade to bring out the awesomeness in our clients.
What we want to see:
- Inspirational and persuasive imagery that relate to Branding.
- No cliche images eg. business man, suits and hand shakes
- We want to transform and educate our clients.
- We want to show them the path and would like our website to really act as a guide that guides them step by step through our process.
- We want the portray that we are an investment but not have a pretentious way to it. We put our heart into every project and that is how we treat our clients.
-When you submit your design please include what platform you have created for. Preference would be Wordpress or Joobla.

We have included the psd file for the wire frame, logo files, font files, site map and a link to a video we create to give you more information on what we would like to see. http://clipvault.example/t/qk82LmZpr

Feel free to make small modification to the logos if you think it will improve it. Your creativity and advice is most welcome.
Updates

One thing we forgot. We would like to have our contact information near the top of the website as well as at the bottom.  Here is out contact info:

Email: info@maplebeacon.example
Phone: 587-555-0142

Project Deadline Extended
Reason: As we are new with the platform and that we want to optimize our results, we decided to extend the deadline by 15 days. Thanks!

Target Market(s)

28-60, Male and Female, Oil field, Local Businesses, Dentists, Chiropractors, Hair salon, Construction/Renovation, Events etc

Industry/Entity Type

Investment

Requirements
Must have
• - 4 Inspirational and persuasive Imagery for the top portion of the website
- Must have a feel as if your not on a website an example of this is linked below.
http://www.artbidhub.example/design/402957/web-design-by-lena-torvik
Nice to have
• - Creative advice from you.
- Creative buttons for Get Free Quote and Subscribe buttons. Something out of the box that draws peoples attention. eg. a 'B' button. Just and example but still something related to branding.
Should not have
• No Cliches

```html
<!DOCTYPE html>
<html lang="en">
<head>
<meta charset="utf-8">
<title>Maple Beacon</title>
<link rel="stylesheet" href="https://fonts.googleapis.com/css2?family=Signika:wght@400;600;700&family=Source+Sans+3:wght@400;600;700&family=PT+Sans+Narrow:wght@700&display=swap">
<style>
  :root {
    --green: #7a9a3a;
    --green-light: #9cbf4c;
    --green-dark: #5f7d27;
    --grey-text: #6d6d6d;
    --grey-tab: #8a8a8c;
    --ink: #2d2d2d;
    --body-text: #444;
    --line: #d4d4d6;
    --footer: #2b2b2b;
    --footer-text: #d8d8d8;
    --white: #fff;
  }
  * { box-sizing: border-box; margin: 0; padding: 0; }
  html, body { width: 1200px; height: 960px; overflow: hidden; background: var(--white); }
  body { position: relative; font-family: "Source Sans 3", sans-serif; color: var(--body-text); }

  .brand-panel {
    position: absolute; left: 10px; top: 6px; width: 300px; height: 400px;
    background: linear-gradient(#fbfbfb, #e9e9ea);
    border: 1px solid var(--line);
  }
  .brand-name {
    position: absolute; left: 22px; top: 14px; display: flex; align-items: center; gap: 14px;
    font-family: "Signika", sans-serif; font-weight: 700; font-size: 36px; line-height: 38px;
    color: var(--grey-text);
  }
  .brand-name .mark { flex: none; width: 24px; height: 24px; border-radius: 50%; background: var(--green); }
  .brand-tagline {
    position: absolute; left: 0; width: 100%; top: 98px; text-align: center;
    font-family: "Signika", sans-serif; font-style: italic; font-size: 19px; color: var(--grey-text);
  }
  .side-nav { position: absolute; left: 30px; top: 142px; list-style: none; }
  .side-nav li {
    width: 238px; height: 38px; margin-bottom: 13.5px; border-radius: 19px;
    background: linear-gradient(#ffffff, #e4e4e5);
    border: 1px solid #cfcfd1; box-shadow: 0 1px 2px rgba(0,0,0,.12);
    display: flex; align-items: center; padding-left: 22px;
    font-family: "PT Sans Narrow", sans-serif; font-weight: 700; font-size: 18px; color: #444;
  }
  .side-nav li::before {
    content: ""; width: 11px; height: 11px; border-radius: 50%; margin-right: 16px;
    background: #f4f4f4; border: 1px solid #bdbdbd;
  }
  .side-nav li.is-active { background: linear-gradient(var(--green-light), var(--green)); color: var(--white); border-color: #b8cc8e; }
  .side-nav li.is-active::before { background: var(--white); border-color: var(--white); }

  .top-tabs { position: absolute; left: 322px; top: 14px; display: flex; gap: 9px; }
  .top-tabs a {
    width: 180px; height: 40px; border-radius: 4px 4px 0 0; text-decoration: none;
    display: flex; align-items: center; justify-content: center;
    font-family: "Signika", sans-serif; font-weight: 700; font-size: 21px; color: var(--white);
    background: linear-gradient(#8db048, var(--green));
    border: 1px solid var(--green-dark); border-bottom: none;
  }
  .top-tabs a.is-current { background: linear-gradient(#9a9a9c, var(--grey-tab)); border-color: #777; }

  .top-contact {
    position: absolute; right: 6px; top: 16px; text-align: right;
    font-size: 10px; line-height: 16px; color: var(--grey-text);
  }

  .hero-frame {
    position: absolute; left: 322px; top: 59px; width: 866px; height: 349px;
    background: var(--green-light); border: 1px solid var(--green);
  }
  .hero-image {
    position: absolute; left: 13px; top: 11px; width: 839px; height: 323px;
    background: linear-gradient(180deg, #8fb45a 0%, #6d7a4a 35%, #5b5a45 65%, #4a4536 100%);
    border: 2px solid var(--white);
  }
  .hero-caption {
    position: absolute; right: 44px; bottom: 40px;
    font-family: "Signika", sans-serif; font-weight: 700; font-size: 34px; color: var(--white);
  }

  .connect-band {
    position: absolute; left: 0; top: 415px; width: 1200px; height: 79px;
    background: linear-gradient(#ffffff, #ececed);
    border-top: 1px solid var(--line);
    box-shadow: 0 4px 8px rgba(0,0,0,.18); z-index: 2;
  }
  .connect-title {
    position: absolute; left: 12px; top: 12px; line-height: 28px;
    font-family: "Signika", sans-serif; font-weight: 600; font-size: 22px; color: var(--grey-text);
  }
  .social-list { position: absolute; left: 106px; top: 22px; display: flex; gap: 7px; }
  .social-list span {
    width: 36px; height: 36px; border-radius: 50%;
    border: 2px solid #d6d6d8; background: #4f7fb6;
  }
  .social-list span:nth-child(2) { background: #6cb9dd; }
  .social-list span:nth-child(3) { background: #3d6f9e; }
  .social-list span:nth-child(4) { background: #e26b1f; }
  .social-list span:nth-child(5) { background: #c5282a; }
  .newsletter-label {
    position: absolute; left: 365px; top: 28px;
    font-size: 17px; font-weight: 600; color: #333;
  }
  .newsletter-field {
    position: absolute; left: 731px; top: 21px; width: 225px; height: 37px;
    background: var(--white); border: 1px solid #cfcfd1; border-radius: 5px;
  }
  .subscribe-button {
    position: absolute; left: 970px; top: 21px; width: 175px; height: 37px; border-radius: 5px;
    background: linear-gradient(#8db048, var(--green-dark)); border: 1px solid #4e6a1f;
    display: flex; align-items: center; justify-content: center;
    font-family: "Signika", sans-serif; font-weight: 700; font-size: 17px; color: var(--white);
  }

  .content-area {
    position: absolute; left: 0; top: 494px; width: 1200px; height: 364px;
    background: linear-gradient(#ffffff, #eeeef0);
  }
  .welcome-panel {
    position: absolute; left: 205px; top: 0; width: 785px; height: 362px;
    background: linear-gradient(#ffffff, #f0f0f2);
    border: 1px solid var(--line); border-top: none; border-radius: 0 0 6px 6px;
  }
  .welcome-title {
    position: absolute; left: 24px; top: 34px; padding-bottom: 6px; width: 362px;
    border-bottom: 1px solid var(--line);
    font-family: "Signika", sans-serif; font-weight: 700; font-size: 28px; color: var(--grey-text);
  }
  .welcome-title em, .quote-title em { font-style: normal; color: var(--green); }
  .welcome-lead { position: absolute; left: 27px; top: 92px; font-size: 16px; font-weight: 600; color: var(--ink); }
  .welcome-copy { position: absolute; left: 28px; top: 120px; width: 730px; }
  .welcome-copy p, .quote-copy {
    font-size: 14.6px; line-height: 22.5px; text-align: justify; color: var(--body-text);
  }
  .welcome-copy p + p { margin-top: 22.5px; }
  .action-button {
    position: absolute; height: 40px;
    background: var(--green); color: var(--white);
    display: flex; align-items: center; justify-content: center;
    font-family: "PT Sans Narrow", sans-serif; font-weight: 700; font-size: 20px;
    box-shadow: 0 1px 2px rgba(0,0,0,.25);
  }
  .learn-more { left: 635px; top: 305px; width: 101px; }

  .quote-panel { position: absolute; left: 990px; top: 0; width: 204px; height: 362px; }
  .quote-title {
    position: absolute; left: 0; top: 38px; width: 204px; padding: 0 0 8px 15px;
    border-bottom: 1px solid var(--line);
    font-family: "Signika", sans-serif; font-weight: 700; font-size: 20px; color: var(--grey-text);
  }
  .quote-copy { position: absolute; left: 16px; top: 80px; width: 174px; }
  .quote-button { left: 14px; top: 304px; width: 177px; font-size: 21px; }

  .site-footer {
    position: absolute; left: 0; top: 858px; width: 1200px; height: 102px;
    background: radial-gradient(ellipse at 50% 0%, #3a3a3a, var(--footer) 70%);
    color: var(--footer-text);
  }
  .footer-links {
    position: absolute; left: 0; width: 1140px; top: 22px; text-align: center;
    font-size: 14.5px; list-style: none;
  }
  .footer-links li { display: inline; }
  .footer-links li + li::before { content: "|"; margin: 0 13px; }
  .footer-copy { position: absolute; left: 0; width: 1140px; top: 60px; text-align: center; font-size: 14px; }
  .footer-copy span + span::before { content: "|"; margin: 0 12px; }
</style>
</head>
<body>

<header class="brand-panel">
  <div class="brand-name"><span class="mark"></span><span>Maple<br>Beacon</span></div>
  <p class="brand-tagline">Because You’re Awesome!</p>
  <ul class="side-nav">
    <li class="is-active">STRATEGY</li>
    <li>PORTFOLIO</li>
    <li>ABOUT US</li>
    <li>CONTACT US</li>
    <li>BLOG</li>
  </ul>
</header>

<nav class="top-tabs">
  <a class="is-current">Maple Beacon</a>
  <a>Be Found</a>
  <a>Connect</a>
  <a>Get Growing</a>
</nav>

<address class="top-contact">info@maplebeacon.example<br>587-555-0142</address>

<section class="hero-frame">
  <div class="hero-image" role="img" aria-label="Close-up of a young green seedling sprouting from soil in a planting tray"></div>
  <p class="hero-caption">Maple Beacon</p>
</section>

<section class="connect-band">
  <p class="connect-title">Connect<br>With Us!</p>
  <div class="social-list" aria-label="Social links">
    <span></span><span></span><span></span><span></span><span></span>
  </div>
  <p class="newsletter-label">Get Tips and Tricks! Subscribe to our Newsletter.</p>
  <div class="newsletter-field"></div>
  <div class="subscribe-button">SUBSCRIBE</div>
</section>

<main class="content-area">
  <article class="welcome-panel">
    <h1 class="welcome-title">Welcome to <em>Maple Beacon</em></h1>
    <p class="welcome-lead">Mauris vel lacus vitae felis vestibulum volutpat. Etiam est nunc, venisl.</p>
    <div class="welcome-copy">
      <p>Sed ut perspiciatis unde omnis iste natus error sit voluptatem accusantium doloremque laudantium, totam rem aperiam, eaque ipsa quae ab illo inventore veritatis et quasi architecto beatae vitae dicta sunt explicabo. Nemo enim ipsam voluptatem quia voluptas sit aspernatur aut odit aut fugit.</p>
      <p>Sed ut perspiciatis unde omnis iste natus error sit voluptatem accusantium doloremque laudantium, totam rem aperiam, eaque ipsa quae ab illo inventore veritatis et quasi architecto beatae vitae dicta sunt explicabo. Nemo enim ipsam voluptatem quia voluptas sit aspernatur aut odit aut fugit, sed quia consequuntur magni dolores eos qui ratione voluptatem sequi nesciunt. Neque porro quisquam est, qui dolorem ipsum quia dolor sit amet.</p>
    </div>
    <div class="action-button learn-more">learn more</div>
  </article>

  <aside class="quote-panel">
    <h2 class="quote-title">Get a <em>Quote Now</em></h2>
    <p class="quote-copy">Sed ut perspiciatis unde omnis iste natus error sit voluptatem accusantium doloremque laudantium, totam rem aperiam, eaque ipsa quae ab natur aut odit aut rem aperiam, eaque ipsa quae ab natur aut odit aut fugit.</p>
    <div class="action-button quote-button">Get A Free Quote</div>
  </aside>
</main>

<footer class="site-footer">
  <ul class="footer-links">
    <li>Site Map</li><li>Strategy</li><li>Portfolio</li><li>About Us</li><li>Contact Us</li><li>Blog</li>
  </ul>
  <p class="footer-copy"><span>©MAPLE BEACON INC. 2013</span><span>info@maplebeacon.example</span><span>587-555-0142</span></p>
</footer>

</body>
</html>
```